Dalvick's Business Card

I need some designs for a new business card including the new logo attached. An old example of our business card is also attached to show all the data that should be included on the new design.
**I added some more examples someone had mocked up**

Contact Information for Business Card

Should include all info on other examples uploaded.

```html
<!DOCTYPE html>
<html lang="en">
<head>
<meta charset="utf-8">
<title>Dalvick's Business Card</title>
<link rel="stylesheet" href="https://fonts.googleapis.com/css2?family=Montserrat:wght@500;600;800&display=swap">
<style>
  :root {
    --brand-blue: #0b72b9;
    --brand-red: #e3202b;
    --paper: #ffffff;
    --stage: #e4e4e6;
    --mark-grey: #ececee;
    --text-blue: #1374bb;
  }
  * { margin: 0; padding: 0; box-sizing: border-box; }
  html, body {
    width: 1200px; height: 1200px; overflow: hidden;
    background: var(--stage);
    font-family: "Montserrat", Arial, sans-serif;
  }
  .sheet {
    position: relative; width: 1200px; height: 1200px;
    display: flex; flex-direction: column; align-items: center; justify-content: center; gap: 56px;
  }
  .card {
    position: relative; width: 900px; height: 514px;
    background: var(--paper);
    box-shadow: 0 18px 40px rgba(0,0,0,0.18);
    overflow: hidden;
  }
  .card-bands { position: absolute; inset: 0; }
  .band-text {
    position: absolute; color: var(--paper);
    text-transform: uppercase; font-size: 22px; line-height: 1.3; letter-spacing: 0.5px;
    font-weight: 500; white-space: nowrap;
  }
  .band-text strong { font-weight: 800; }
  .band-text--area { left: 60px; top: 34px; }
  .band-text--call { left: 380px; bottom: 34px; text-align: left; }
  .wordmark {
    display: flex; align-items: center; gap: 18px;
    color: var(--brand-blue); font-weight: 800; text-transform: uppercase; letter-spacing: 2px;
    white-space: nowrap;
  }
  .wordmark-dot { border-radius: 50%; background: var(--brand-red); flex: none; }
  .card-front .wordmark {
    position: absolute; left: 50%; top: 50%; transform: translate(-50%, -50%);
    font-size: 96px;
  }
  .card-front .wordmark-dot { width: 54px; height: 54px; }
  .back-mark {
    position: absolute; left: 60px; top: 92px; width: 330px; height: 330px;
    border-radius: 50%; border: 30px solid var(--mark-grey);
  }
  .contact {
    position: absolute; right: 60px; top: 64px;
    display: flex; flex-direction: column; align-items: flex-end;
    color: var(--text-blue); text-transform: uppercase; font-weight: 500;
  }
  .card-back .wordmark { font-size: 52px; gap: 12px; margin-bottom: 38px; }
  .card-back .wordmark-dot { width: 30px; height: 30px; }
  .contact-name { color: var(--brand-red); font-weight: 800; font-size: 40px; letter-spacing: 1px; margin-bottom: 14px; }
  .contact-line { display: flex; align-items: center; gap: 10px; font-size: 27px; line-height: 1.35; }
  .contact-line--lower { text-transform: none; }
  .contact-line svg { width: 22px; height: 22px; fill: var(--brand-red); }
  .contact-claim { font-size: 27px; line-height: 1.35; letter-spacing: 0.5px; }
  .contact-claim:first-of-type { margin-top: 6px; }
</style>
</head>
<body>
<main class="sheet">
  <section class="card card-front" aria-label="Card front">
    <svg class="card-bands" viewBox="0 0 900 514" aria-hidden="true">
      <polygon points="0,0 560,0 500,118 0,118" fill="var(--brand-blue)"/>
      <polygon points="280,514 340,390 900,390 900,514" fill="var(--brand-blue)"/>
    </svg>
    <p class="band-text band-text--area">Serves Millbrook, IA &amp;<br><strong>Surrounding Areas</strong></p>
    <div class="wordmark"><span class="wordmark-dot"></span>Dalvick's</div>
    <p class="band-text band-text--call">Call today for all your <strong>HVAC,</strong><br><strong>Refrigeration</strong> &amp; <strong>Plumbing Needs</strong></p>
  </section>

  <section class="card card-back" aria-label="Card back">
    <div class="back-mark" aria-hidden="true"></div>
    <div class="contact">
      <div class="wordmark"><span class="wordmark-dot"></span>Dalvick's</div>
      <p class="contact-name">Mark Dalvick</p>
      <p class="contact-line">555.014.0187
        <svg viewBox="0 0 24 24" aria-hidden="true"><path d="M6.6 10.8a15 15 0 0 0 6.6 6.6l2.2-2.2c.3-.3.7-.4 1-.2 1.1.4 2.3.6 3.6.6.6 0 1 .4 1 1V20c0 .6-.4 1-1 1C10.6 21 3 13.4 3 4c0-.6.4-1 1-1h3.5c.6 0 1 .4 1 1 0 1.3.2 2.5.6 3.6.1.3 0 .7-.2 1z"/></svg>
      </p>
      <p class="contact-line contact-line--lower">hvacdalvick@mailbox.com
        <svg viewBox="0 0 24 24" aria-hidden="true"><path d="M2 5h20v14H2z M2 5l10 8 10-8" stroke="#fff" stroke-width="1.5"/></svg>
      </p>
      <p class="contact-claim">Licensed &amp; Insured</p>
      <p class="contact-claim">Family Owned &amp; Operated</p>
    </div>
  </section>
</main>
</body>
</html>
```